Modern Verdell Tree Care Website

I need a website for a full service Tree Care company. The company provides tree pruning, tree removal, tree preservation, emergency services, stump grinding, and emergency tree services.

Target Market(s)

Customers that need tree services

Industry/Entity Type

Landscaping, Tree Services

Coding

Coded - Design and coding required

Number of Pages Required

5+ page

Font styles to use
Sans Serif

Requirements
Must have
• Good clean design that showcases the services the company provides.
Nice to have
• Services page; contact form, blog, home page, about page

```html
<!DOCTYPE html>
<html lang="en">
<head>
<meta charset="utf-8">
<title>Verdell Tree Care</title>
<link href="https://fonts.googleapis.com/css2?family=Montserrat:wght@400;500;600;700;800&family=Josefin+Sans:wght@300;400;600&display=swap" rel="stylesheet">
<style>
:root{
  --green:#8cc63f;
  --green-dark:#4f7a22;
  --orange:#f7a631;
  --ink:#222222;
  --text:#3d3d3d;
  --beige:#f1efe6;
  --tan:#b08a5f;
  --white:#ffffff;
  --line:#d9d9d9;
}
*{margin:0;padding:0;box-sizing:border-box}
html,body{width:1200px;height:4295px;overflow:hidden;background:var(--white)}
body{position:relative;font-family:"Josefin Sans",sans-serif;color:var(--text)}
.page{position:relative;width:1200px;height:4295px}
section,header,footer{position:absolute;left:0;width:1200px}
.abs{position:absolute}
.heading{font-family:"Montserrat",sans-serif;font-weight:700;color:var(--ink);text-transform:uppercase;letter-spacing:.5px}
.heading .accent{color:var(--green);font-weight:400}
.underline{position:absolute;height:3px;width:60px;background:var(--green)}
.btn{position:absolute;display:flex;align-items:center;justify-content:center;font-family:"Montserrat",sans-serif;font-weight:600;color:var(--white);background:var(--orange);border-radius:30px;text-transform:uppercase}

/* header */
.site-header{top:0;height:82px;background:var(--white);z-index:5}
.brand{position:absolute;display:flex;align-items:center;gap:12px;font-family:"Montserrat",sans-serif;font-weight:700;color:#5a5a5a;letter-spacing:1px}
.brand-dot{width:30px;height:30px;border-radius:50%;background:var(--green)}
.main-nav{position:absolute;left:335px;top:0;height:82px;display:flex;align-items:center;font-family:"Montserrat",sans-serif;font-size:14px;font-weight:500;color:#444;letter-spacing:1px}
.main-nav a{text-decoration:none;color:inherit;position:relative}
.main-nav .sep{color:#bbb;margin:0 30px}
.main-nav .active{color:var(--green)}
.main-nav .active::after{content:"";position:absolute;left:0;right:0;bottom:-10px;height:2px;background:var(--green)}
.header-phone{position:absolute;right:0;top:0;width:235px;height:82px;background:var(--green);clip-path:polygon(18px 0,100% 0,100% 100%,0 100%);display:flex;align-items:center;padding-left:30px;gap:10px;color:var(--white);font-family:"Montserrat",sans-serif;font-size:16px;letter-spacing:1.5px}
.icon-circle{width:26px;height:26px;border-radius:50%;background:var(--white);display:flex;align-items:center;justify-content:center}

/* hero */
.hero{top:82px;height:690px;overflow:hidden}
.hero-photo{position:absolute;inset:0;background:linear-gradient(100deg,#6f7c4a 0%,#c7d4e0 30%,#e9eef3 50%,#b9c4cf 70%,#7b6a4e 100%)}
.hero-title{position:absolute;left:0;width:1200px;text-align:center}
.hero-welcome{top:175px;font-family:"Josefin Sans",sans-serif;font-size:36px;color:#333;letter-spacing:1px}
.hero-welcome::before,.hero-welcome::after{content:"";display:inline-block;width:88px;height:2px;background:var(--green);vertical-align:middle;margin:0 12px 8px}
.hero-name{top:218px;font-family:"Montserrat",sans-serif;font-weight:800;font-size:53px;color:#2d2d2d}
.hero-sub{top:288px;font-size:22px;color:#333}
.hero-arrow{position:absolute;top:240px}
.hero-wave{position:absolute;left:0;bottom:0}

/* about */
.about{top:772px;height:500px}
.about-ring{position:absolute;left:84px;top:-12px;width:460px;height:460px;border-radius:50%;border:8px solid var(--green);border-right-color:transparent;transform:rotate(25deg)}
.about-photo-main{position:absolute;left:105px;top:8px;width:432px;height:432px;border-radius:50%;background:radial-gradient(circle at 45% 40%,#9cc96a,#3f6d25 75%)}
.about-photo-small{position:absolute;left:318px;top:255px;width:254px;height:254px;border-radius:50%;border:6px solid var(--orange);background:radial-gradient(circle at 50% 40%,#c6b488,#557a2c 70%)}
.about-title{position:absolute;left:610px;top:28px;font-size:40px;line-height:42px}
.about-text{position:absolute;left:618px;top:150px;width:510px;font-size:15.5px;line-height:23px;color:#444}
.about-text p+p{margin-top:22px}

/* services */
.services{top:1262px;height:773px;background:var(--beige)}
.services-curve{position:absolute;left:0;top:0}
.section-title{position:absolute;left:0;width:1200px;text-align:center;font-size:36px}
.service-card{position:absolute;width:300px;height:215px;border-radius:28px 0 28px 0;overflow:hidden}
.service-card .photo{position:absolute;inset:0}
.service-card .label{position:absolute;left:0;right:0;bottom:26px;text-align:center;font-family:"Montserrat",sans-serif;font-weight:700;font-size:16px;color:var(--white);letter-spacing:.3px}
.service-card .label::after{content:"";display:block;width:38px;height:3px;background:var(--white);margin:10px auto 0}
.service-card.featured .photo{background:#3c5a20}
.featured-body{position:absolute;inset:0;text-align:center;color:var(--white);padding:38px 28px 0}
.featured-body h3{font-family:"Montserrat",sans-serif;font-weight:600;font-size:17px;letter-spacing:.5px}
.featured-body p{font-size:11.5px;line-height:16px;margin-top:12px}
.featured-body .mini-btn{display:inline-block;margin-top:12px;background:var(--green);font-family:"Montserrat",sans-serif;font-size:8px;font-weight:700;padding:8px 24px;border-radius:14px}

/* why */
.why{top:2035px;height:705px;background:var(--white)}
.why-tree{position:absolute;left:430px;top:145px;width:345px;height:320px;border-radius:48% 48% 40% 40%;background:radial-gradient(circle at 50% 40%,#5f9b32,#2d5d18 75%)}
.feature{position:absolute;width:80px;height:80px;border-radius:50%;display:flex;align-items:center;justify-content:center}
.feature.g{background:var(--green)}
.feature.o{background:var(--orange)}
.feature-label{position:absolute;font-family:"Montserrat",sans-serif;font-weight:600;font-size:16px;line-height:21px;color:#333;text-transform:uppercase}
.feature-label.right{text-align:right}

/* blogs */
.blogs{top:2740px;height:640px;background:var(--beige)}
.blog-card{position:absolute;top:147px;width:322px;height:391px;background:var(--white);border:1px solid #d3d3d3}
.blog-card .photo{position:absolute;left:0;top:0;width:100%;height:218px}
.blog-date{position:absolute;left:0;top:188px;width:130px;height:30px;background:var(--tan);color:var(--white);font-family:"Montserrat",sans-serif;font-weight:600;font-size:12px;display:flex;align-items:center;justify-content:center}
.blog-card h3{position:absolute;left:32px;top:242px;width:260px;font-family:"Montserrat",sans-serif;font-weight:600;font-size:16px;line-height:22px;color:#222}
.blog-card p{position:absolute;left:32px;top:298px;width:265px;font-size:11px;line-height:18px;color:#444}
.blog-card a{position:absolute;left:30px;top:342px;font-family:"Montserrat",sans-serif;font-weight:600;font-size:13px;color:var(--green);text-decoration:underline}

/* contact */
.contact{top:3380px;height:562px;background:var(--green);overflow:hidden}
.contact-photo{position:absolute;inset:0;clip-path:polygon(773px 0,1200px 0,1200px 562px,480px 562px);background:linear-gradient(160deg,#2f6fc0 0%,#4d8fd8 40%,#6e7b52 75%,#4c5a2e 100%)}
.contact-stripe{position:absolute;inset:0;background:var(--orange);clip-path:polygon(718px 95px,728px 95px,538px 540px,528px 540px)}
.contact-title{position:absolute;left:113px;top:78px;font-size:36px;color:var(--white)}
.field{position:absolute;left:117px;width:416px;background:var(--white);font-size:13px;color:#444;padding:0 24px;display:flex;align-items:center}
.field.area{align-items:flex-start;padding-top:20px}
.send-btn{position:absolute;left:114px;top:422px;width:171px;height:42px;border-radius:22px;background:#2b2f33;color:var(--white);font-family:"Montserrat",sans-serif;font-weight:600;font-size:13px;display:flex;align-items:center;justify-content:center}

/* footer */
.site-footer{top:3942px;height:353px;background:var(--white)}
.footer-rule{position:absolute;left:100px;width:998px;height:1px;background:#cfcfcf}
.footer-nav{position:absolute;left:0;top:160px;width:1200px;display:flex;justify-content:center;align-items:center;font-family:"Montserrat",sans-serif;font-weight:600;font-size:15px;color:#222}
.footer-nav .dot{width:5px;height:5px;border-radius:50%;background:var(--green);margin:0 40px}
.footer-contacts{position:absolute;top:248px;left:0;width:1200px;font-family:"Montserrat",sans-serif;font-size:14px;font-weight:500;color:#222}
.contact-item{position:absolute;display:flex;align-items:center;gap:10px}
.contact-item .bubble{width:34px;height:34px;border-radius:50%;background:var(--green);display:flex;align-items:center;justify-content:center}
.social{position:absolute;top:0;display:flex;gap:14px;left:926px}
.social span{width:26px;height:26px;border-radius:50%;border:2px solid #444}
.social span.alt{border-color:var(--green)}
.copyright{position:absolute;left:0;top:298px;width:1200px;height:55px;background:var(--tan);color:var(--white);font-size:14px;display:flex;align-items:center;justify-content:center}
</style>
</head>
<body>
<div class="page">

<header class="site-header">
  <div class="brand" style="left:85px;top:22px;font-size:24px"><span class="brand-dot"></span>VERDELL TREE CARE</div>
  <nav class="main-nav">
    <a class="active" href="#">HOME</a><span class="sep">|</span>
    <a href="#">ABOUT US</a><span class="sep">|</span>
    <a href="#">SERVICES</a><span class="sep">|</span>
    <a href="#">BLOG</a><span class="sep">|</span>
    <a href="#">CONTACT US</a>
  </nav>
  <div class="header-phone">
    <span class="icon-circle"><svg width="14" height="14" viewBox="0 0 24 24"><path fill="#8cc63f" d="M6.6 10.8a15.1 15.1 0 0 0 6.6 6.6l2.2-2.2c.3-.3.7-.4 1-.2 1.1.4 2.3.6 3.6.6.6 0 1 .4 1 1V20c0 .6-.4 1-1 1C10.6 21 3 13.4 3 4c0-.6.4-1 1-1h3.5c.6 0 1 .4 1 1 0 1.3.2 2.5.6 3.6.1.3 0 .7-.2 1z"/></svg></span>
    (555) 214 7730
  </div>
</header>

<section class="hero">
  <div class="hero-photo" role="img" aria-label="Arborists at work: one in a bucket lift trimming branches, another with a chainsaw, against a bright sky and tree canopy"></div>
  <svg class="hero-arrow" style="left:28px" width="22" height="40" viewBox="0 0 22 40"><path d="M18 4 4 20l14 16" fill="none" stroke="#8cc63f" stroke-width="3"/></svg>
  <svg class="hero-arrow" style="left:1150px" width="22" height="40" viewBox="0 0 22 40"><path d="M4 4l14 16L4 36" fill="none" stroke="#ffffff" stroke-width="3"/></svg>
  <div class="hero-title hero-welcome">WELCOME TO</div>
  <h1 class="hero-title hero-name">VERDELL TREE CARE</h1>
  <p class="hero-title hero-sub">Serving Maplewood and surrounding areas.</p>
  <div class="btn" style="left:500px;top:333px;width:163px;height:48px;font-size:14px">Contact Us</div>
  <svg class="hero-wave" width="1200" height="120" viewBox="0 0 1200 120">
    <path d="M0 80 Q600 -10 1200 60 L1200 82 Q600 20 0 120 Z" fill="#8cc63f"/>
    <path d="M0 120 Q600 20 1200 82 L1200 120 Z" fill="#ffffff"/>
  </svg>
</section>

<section class="about">
  <div class="about-ring"></div>
  <div class="about-photo-main" role="img" aria-label="Close-up of pruning shears cutting a green branch"></div>
  <div class="about-photo-small" role="img" aria-label="Gardener trimming a hedge with a power trimmer"></div>
  <h2 class="heading about-title">About Verdell<br><span class="accent">Tree Care</span></h2>
  <div class="about-text">
    <p>At Verdell Tree Care, we are more than just a tree service company, we are stewards of our beautiful trees. With a passion deeply rooted in arboriculture, we embark on a mission to promote the health, beauty, and safety of your trees and landscapes.</p>
    <p>Whether it's expert tree trimming to enhance aesthetics, meticulous tree removal to mitigate hazards, or comprehensive tree health assessments to ensure safety , we approach each task with unwavering dedication and attention to detail.</p>
  </div>
  <div class="btn" style="left:615px;top:383px;width:193px;height:52px;font-size:15px">Learn More</div>
</section>

<section class="services">
  <svg class="services-curve" width="1200" height="90" viewBox="0 0 1200 90">
    <path d="M0 0 L1200 0 L1200 8 Q640 110 0 8 Z" fill="#ffffff"/>
    <path d="M0 8 Q640 110 1200 8" fill="none" stroke="#f7a631" stroke-width="4"/>
  </svg>
  <h2 class="heading section-title" style="top:150px">Services <span class="accent">Provide</span></h2>
  <div class="underline" style="left:570px;top:200px"></div>

  <div class="service-card" style="left:120px;top:238px">
    <div class="photo" role="img" aria-label="Pruning shears cutting a tree branch" style="background:linear-gradient(160deg,#9bb86a,#5d6b4a 60%,#3a4a2a)"></div>
    <div class="label">TREE PRUNING</div>
  </div>
  <div class="service-card featured" style="left:447px;top:238px">
    <div class="photo" role="img" aria-label="Tree removal work in a wooded area, dimmed behind text"></div>
    <div class="featured-body">
      <h3>TREE REMOVAL</h3>
      <p>Lorem ipsum dolor sit amet, consectetur adipiscing elit, sed do eiusmod tempor incididunt ut labore et dolore</p>
      <span class="mini-btn">LEARN MORE</span>
    </div>
  </div>
  <div class="service-card" style="left:773px;top:238px">
    <div class="photo" role="img" aria-label="Shovel digging soil beside a young tree" style="background:linear-gradient(160deg,#8dbd55,#6b4a30 55%,#3f5a24)"></div>
    <div class="label">TREE PRESERVATION</div>
  </div>
  <div class="service-card" style="left:117px;top:478px">
    <div class="photo" role="img" aria-label="Large tree stump being ground down" style="background:linear-gradient(160deg,#5a7a3a,#8a6a45 55%,#3a3222)"></div>
    <div class="label">STUMP GRINDING</div>
  </div>
  <div class="service-card" style="left:443px;top:478px">
    <div class="photo" role="img" aria-label="Fallen tree after a storm" style="background:linear-gradient(160deg,#7ea25a,#5a6a48 55%,#2f3a22)"></div>
    <div class="label">TREE EMERGENCY SERVICES</div>
  </div>
  <div class="service-card" style="left:770px;top:478px">
    <div class="photo" role="img" aria-label="Arborist in a harness installing cables in a tree" style="background:linear-gradient(160deg,#6e96c8,#8a7a5a 55%,#3f4a2a)"></div>
    <div class="label">CABLING &amp; BRACING</div>
  </div>
</section>

<section class="why">
  <h2 class="heading section-title" style="top:70px">Why Choose <span class="accent">Verdell</span></h2>
  <div class="underline" style="left:570px;top:114px"></div>
  <svg class="abs" style="left:0;top:0" width="1200" height="705" viewBox="0 0 1200 705">
    <path d="M338 175 A262 265 0 1 0 865 185" fill="none" stroke="#f7a631" stroke-width="1.5"/>
  </svg>
  <div class="why-tree" role="img" aria-label="Large, full green tree"></div>

  <div class="feature g" style="left:333px;top:135px"><svg width="40" height="40" viewBox="0 0 40 40" fill="none" stroke="#fff" stroke-width="2"><rect x="9" y="6" width="22" height="28" rx="2"/><path d="M14 20l4 4 8-9"/></svg></div>
  <div class="feature-label right" style="right:892px;top:153px">Licensed and<br>Insured</div>

  <div class="feature o" style="left:305px;top:293px"><svg width="40" height="40" viewBox="0 0 40 40" fill="none" stroke="#fff" stroke-width="2"><circle cx="20" cy="20" r="13"/><path d="M20 12v8l6 4"/></svg></div>
  <div class="feature-label right" style="right:907px;top:318px">24 Hour Emergency<br>Services</div>

  <div class="feature g" style="left:375px;top:448px"><svg width="40" height="40" viewBox="0 0 40 40" fill="none" stroke="#fff" stroke-width="2"><path d="M20 35s-10-11-10-18a10 10 0 0 1 20 0c0 7-10 18-10 18z"/><circle cx="20" cy="17" r="4"/></svg></div>
  <div class="feature-label right" style="right:842px;top:473px">Locally Owned<br>&amp; Operated</div>

  <div class="feature o" style="left:555px;top:522px"><svg width="40" height="40" viewBox="0 0 40 40" fill="none" stroke="#fff" stroke-width="2"><circle cx="20" cy="13" r="5"/><circle cx="10" cy="22" r="3.5"/><circle cx="30" cy="22" r="3.5"/><path d="M11 33c0-6 4-10 9-10s9 4 9 10"/></svg></div>
  <div class="feature-label" style="left:0;width:1195px;text-align:center;top:617px">Licensed Arborist<br>On Staff</div>

  <div class="feature g" style="left:760px;top:452px"><svg width="40" height="40" viewBox="0 0 40 40" fill="none" stroke="#fff" stroke-width="2"><rect x="11" y="7" width="18" height="26" rx="2"/><path d="M15 14h10M15 20h10M15 26h6"/></svg></div>
  <div class="feature-label" style="left:852px;top:483px">Free Estimate</div>

  <div class="feature o" style="left:818px;top:297px"><svg width="40" height="40" viewBox="0 0 40 40" fill="none" stroke="#fff" stroke-width="2"><path d="M20 6l12 5v8c0 8-5 13-12 15-7-2-12-7-12-15v-8z"/><path d="M15 20l4 4 7-8"/></svg></div>
  <div class="feature-label" style="left:910px;top:314px">Safety is our<br>top priority</div>

  <div class="feature g" style="left:790px;top:145px"><svg width="40" height="40" viewBox="0 0 40 40" fill="none" stroke="#fff" stroke-width="2"><circle cx="20" cy="15" r="9"/><path d="M20 24v11M15 35h10"/></svg></div>
  <div class="feature-label" style="left:885px;top:163px">Professional<br>Work</div>
</section>

<section class="blogs">
  <h2 class="heading abs" style="left:100px;top:60px;font-size:36px">Latest <span class="accent">Blogs</span></h2>
  <div class="underline" style="left:100px;top:108px"></div>

  <article class="blog-card" style="left:98px">
    <div class="photo" role="img" aria-label="Chainsaw cutting into a tree trunk" style="background:linear-gradient(150deg,#7c8a6a,#a9a196 50%,#5a5246)"></div>
    <span class="blog-date">20 MAY 2024</span>
    <h3>Lorem ipsum dolor sit amet consectetur adipiscing</h3>
    <p>Lorem ipsum dolor sit amet, consectetur adipiscing elit, sed do eiusmod tempor incid</p>
    <a href="#">LEARN MORE</a>
  </article>
  <article class="blog-card" style="left:445px">
    <div class="photo" role="img" aria-label="Arborist climbing a tree with a chainsaw" style="background:linear-gradient(150deg,#8fb862,#b8b4a8 50%,#4f6a30)"></div>
    <span class="blog-date">20 MAY 2024</span>
    <h3>Lorem ipsum dolor sit amet consectetur adipiscing</h3>
    <p>Lorem ipsum dolor sit amet, consectetur adipiscing elit, sed do eiusmod tempor incid</p>
    <a href="#">LEARN MORE</a>
  </article>
  <article class="blog-card" style="left:788px">
    <div class="photo" role="img" aria-label="Worker cutting a branch with long loppers" style="background:linear-gradient(150deg,#9ac46a,#6f8a52 50%,#3f5a26)"></div>
    <span class="blog-date">20 MAY 2024</span>
    <h3>Lorem ipsum dolor sit amet consectetur adipiscing</h3>
    <p>Lorem ipsum dolor sit amet, consectetur adipiscing elit, sed do eiusmod tempor incid</p>
    <a href="#">LEARN MORE</a>
  </article>
</section>

<section class="contact">
  <div class="contact-photo" role="img" aria-label="Arborist in safety gear and harness climbing a tall tree against a blue sky"></div>
  <div class="contact-stripe"></div>
  <h2 class="heading contact-title">Contact Us</h2>
  <div class="field" style="top:153px;height:42px">First Name*</div>
  <div class="field" style="top:208px;height:42px">Email address</div>
  <div class="field" style="top:263px;height:42px">Phone number</div>
  <div class="field area" style="top:318px;height:87px">Leave Message</div>
  <div class="send-btn">SEND MESSAGE</div>
</section>

<footer class="site-footer">
  <div class="brand" style="left:0;width:1200px;justify-content:center;top:52px;font-size:30px"><span class="brand-dot" style="width:36px;height:36px"></span>VERDELL TREE CARE</div>
  <div class="footer-rule" style="top:136px"></div>
  <nav class="footer-nav">
    <span>HOME</span><span class="dot"></span><span>ABOUT US</span><span class="dot"></span><span>SERVICES</span><span class="dot"></span><span>BLOGS</span><span class="dot"></span><span>REVIEWS</span><span class="dot"></span><span>CONTACT</span>
  </nav>
  <div class="footer-rule" style="top:203px"></div>
  <div class="footer-contacts">
    <div class="contact-item" style="left:195px;top:-4px"><span class="bubble"><svg width="16" height="16" viewBox="0 0 24 24"><path fill="#fff" d="M6.6 10.8a15.1 15.1 0 0 0 6.6 6.6l2.2-2.2c.3-.3.7-.4 1-.2 1.1.4 2.3.6 3.6.6.6 0 1 .4 1 1V20c0 .6-.4 1-1 1C10.6 21 3 13.4 3 4c0-.6.4-1 1-1h3.5c.6 0 1 .4 1 1 0 1.3.2 2.5.6 3.6.1.3 0 .7-.2 1z"/></svg></span>(555) 214-7730</div>
    <div class="contact-item" style="left:430px;top:-4px"><span class="bubble"><svg width="16" height="16" viewBox="0 0 24 24"><path fill="#fff" d="M6.6 10.8a15.1 15.1 0 0 0 6.6 6.6l2.2-2.2c.3-.3.7-.4 1-.2 1.1.4 2.3.6 3.6.6.6 0 1 .4 1 1V20c0 .6-.4 1-1 1C10.6 21 3 13.4 3 4c0-.6.4-1 1-1h3.5c.6 0 1 .4 1 1 0 1.3.2 2.5.6 3.6.1.3 0 .7-.2 1z"/></svg></span>(555) 386-4412</div>
    <div class="contact-item" style="left:630px;top:-4px"><span class="bubble"><svg width="16" height="16" viewBox="0 0 24 24" fill="none" stroke="#fff" stroke-width="2"><rect x="3" y="6" width="18" height="12" rx="1"/><path d="M3 7l9 6 9-6"/></svg></span>hello@verdelltreecare.com</div>
    <div class="social"><span></span><span class="alt"></span><span></span><span class="alt"></span></div>
  </div>
  <div class="copyright">Copyright © 2024 Verdell Tree Care | All Right Reserved</div>
</footer>

</div>
</body>
</html>
```